Business Card Design - Property Management & Real Estate Services

I need a business card design for my company that I can print ZEPLA Cards. The company is called Brindle Management Company. It is a property management and real estate company. The design has to be clean and modern. I need two versions. One for my employee and one for me. However, the design will be the same, just different text. You can get a feel for the company by looking at our website at www.brindlemanagement.example.

Industry/Entity Type

Property Management

Contact Information for Business Card

I will be using ZEPLA.com to print my cards. I will most likely use the rounded edges card. I need two versions, however, they will be the same design. I need one for me and my employee.

Colors
3276b5
33a6d7

Requirements
Must have
• Company Logo
• Name of person
• Property Management & Real Estate Service
• Phone
• Email
• Website
• Address
• A space to place a QR code

```html
<!DOCTYPE html>
<html lang="en">
<head>
<meta charset="utf-8">
<title>Brindle Management – Business Card</title>
<link rel="stylesheet" href="https://fonts.googleapis.com/css2?family=Montserrat:wght@500&family=Roboto:wght@400&family=Exo+2:ital,wght@0,600;1,600&display=swap">
<style>
  :root {
    --backdrop: #2f3032;
    --card: #1d1e21;
    --silver: #a9acb1;
    --brand-blue: #3276b5;
    --brand-sky: #33a6d7;
    --band-blue: #2a62ad;
    --strip-blue: #5f97d3;
    --muted: #8b8f96;
    --white: #ffffff;
  }
  * { margin: 0; padding: 0; box-sizing: border-box; }
  html, body {
    width: 799px; height: 1200px; overflow: hidden;
    background: var(--backdrop);
  }
  .sheet {
    position: relative; width: 799px; height: 1200px;
  }
  .card {
    position: absolute; left: 70px;
    width: 660px; height: 377px;
    border-radius: 26px;
    background: var(--card);
    overflow: hidden;
  }
  .card--front { top: 140px; }
  .card--back { top: 690px; }

  .wordmark {
    font-family: "Montserrat", sans-serif;
    font-weight: 500;
    text-transform: uppercase;
    letter-spacing: 0.08em;
    line-height: 1.1;
  }
  .card--front .wordmark {
    position: absolute; left: 0; right: 0; top: 140px;
    text-align: center;
    font-size: 40px;
    color: var(--silver);
  }
  .card--back .wordmark {
    position: absolute; left: 40px; top: 92px;
    font-size: 34px;
    color: var(--brand-blue);
  }

  .contact {
    position: absolute; left: 352px; top: 82px;
    font-family: "Roboto", sans-serif;
    color: var(--brand-blue);
  }
  .contact__name {
    font-family: "Exo 2", sans-serif;
    font-weight: 600; font-style: italic;
    font-size: 22px; color: var(--brand-blue);
  }
  .contact__role {
    font-size: 14px; color: var(--muted);
    margin: 2px 0 16px;
  }
  .contact__list { list-style: none; }
  .contact__item {
    display: flex; align-items: center; gap: 9px;
    font-size: 15.5px; line-height: 24px;
    color: #4d89c9;
  }
  .contact__item svg { width: 13px; height: 13px; flex: none; }
  .contact__item--plain { padding-left: 0; }

  .band {
    position: absolute; left: 0; top: 0;
    width: 660px; height: 377px;
  }
  .tagline {
    position: absolute; right: 34px; bottom: 22px;
    font-family: "Exo 2", sans-serif;
    font-weight: 600;
    font-size: 16.5px;
    color: var(--white);
  }
</style>
</head>
<body>
<main class="sheet">

  <section class="card card--front" aria-label="Card front">
    <p class="wordmark">Brindle Management</p>
  </section>

  <section class="card card--back" aria-label="Card back">
    <svg class="band" viewBox="0 0 660 377" aria-hidden="true">
      <path d="M0 352 H225 L214 377 H0 Z" fill="var(--strip-blue)"/>
      <path d="M205 377 L238 312 Q244 300 258 300 H660 V377 Z" fill="var(--band-blue)"/>
    </svg>

    <p class="wordmark">Brindle<br>Management</p>

    <div class="contact">
      <p class="contact__name">Marcos T. Ellery</p>
      <p class="contact__role">Founder</p>
      <ul class="contact__list">
        <li class="contact__item">
          <svg viewBox="0 0 16 16" aria-hidden="true"><path d="M3 1h3l1.5 4-2 1.3a9 9 0 0 0 4.2 4.2L11 8.5l4 1.5v3a2 2 0 0 1-2 2A12 12 0 0 1 1 3a2 2 0 0 1 2-2z" fill="var(--brand-blue)"/></svg>
          (305) 555-0148
        </li>
        <li class="contact__item">
          <svg viewBox="0 0 16 16" aria-hidden="true"><rect x="1" y="3" width="14" height="10" rx="1.5" fill="var(--brand-blue)"/><path d="M1.5 4 8 9l6.5-5" fill="none" stroke="var(--card)" stroke-width="1.3"/></svg>
          marcos@brindlemanagement.example
        </li>
        <li class="contact__item">
          <svg viewBox="0 0 16 16" aria-hidden="true"><circle cx="8" cy="8" r="6.5" fill="none" stroke="var(--brand-blue)" stroke-width="1.5"/><path d="M1.5 8h13M8 1.5c-3 3.5-3 9.5 0 13M8 1.5c3 3.5 3 9.5 0 13" fill="none" stroke="var(--brand-blue)" stroke-width="1.2"/></svg>
          www.brindlemanagement.example
        </li>
        <li class="contact__item contact__item--plain">
          480 Harbor Ave #210 Miami, FL 33131
        </li>
      </ul>
    </div>

    <p class="tagline">Miami Property Management &amp; Real Estate Services</p>
  </section>

</main>
</body>
</html>
```